Salon and Spa Distributor Business Card

Need a business card. We are are distributor in the salon and spa industry. We identify with natural beauty. Need a card with:
Company Name: Petal Quarry"
Title: "President & CEO"
Address
Company Phone number
email
website
Tag Line:" The Professional Salon Source"

Industry/Entity Type

Business

Contact Information for Business Card

Name: Dov Strommen
Title: "President & CEO"
Address: 31 Harlow Ln, Bexmoor, NJ 07813
Company Phone number: 800-463-5918
email: dovstrommen@petalquarry.example
website: www.petalquarry.example

Requirements
Should not have
• No black backgrounds

```html
<!DOCTYPE html>
<html lang="en">
<head>
<meta charset="utf-8">
<title>Petal Quarry — Business Card</title>
<link rel="stylesheet" href="https://fonts.googleapis.com/css2?family=Open+Sans:wght@400;600;700&display=swap">
<style>
  :root {
    --backdrop: #e6e3df;
    --card-ground: #1d3325;
    --leaf-green: #7ad66a;
    --text-white: #f2f4f0;
    --silver: #d6ddd6;
    --divider: #4a6652;
  }
  * { margin: 0; padding: 0; box-sizing: border-box; }
  html, body {
    width: 1200px; height: 900px; overflow: hidden;
    background: var(--backdrop);
    font-family: "Open Sans", Arial, sans-serif;
  }
  .canvas { position: relative; width: 1200px; height: 900px; }
  .card {
    position: absolute; top: 302px;
    width: 525px; height: 300px;
    background: var(--card-ground);
    box-shadow: 0 10px 28px rgba(0,0,0,.25);
  }
  .card--front { left: 50px; }
  .card--back { left: 625px; }

  /* front */
  .front-brand {
    position: absolute; left: 0; top: 0; width: 228px; height: 300px;
    display: flex; align-items: center; justify-content: center; gap: 9px;
  }
  .brand-dot {
    width: 12px; height: 12px; border-radius: 50%;
    background: var(--leaf-green);
  }
  .brand-name--front {
    color: var(--leaf-green); font-weight: 600; font-size: 23px;
  }
  .front-divider {
    position: absolute; left: 228px; top: 70px;
    width: 1px; height: 160px; background: var(--divider);
  }
  .contact {
    position: absolute; left: 248px; top: 44px; right: 24px;
    color: var(--text-white);
  }
  .contact__name {
    color: var(--leaf-green); font-weight: 700; font-size: 18px; line-height: 1.1;
  }
  .contact__title { font-size: 12.5px; margin-top: 3px; }
  .contact__address { font-size: 13px; line-height: 1.55; margin-top: 22px; }
  .contact__list { list-style: none; margin-top: 20px; font-size: 12.5px; }
  .contact__item {
    display: flex; align-items: center; gap: 8px; line-height: 1.7;
    white-space: nowrap;
  }
  .contact__icon { width: 11px; height: 11px; flex: none; }

  /* back */
  .back-brand {
    position: absolute; inset: 0;
    display: flex; flex-direction: column; align-items: center; justify-content: center;
  }
  .brand-name--back {
    color: var(--silver); font-weight: 400; font-size: 32px; letter-spacing: .5px;
  }
  .tagline { color: var(--silver); font-size: 15px; margin-top: 34px; }
</style>
</head>
<body>
<main class="canvas">
  <section class="card card--front">
    <div class="front-brand">
      <span class="brand-dot"></span>
      <span class="brand-name--front">Petal Quarry</span>
    </div>
    <div class="front-divider"></div>
    <div class="contact">
      <p class="contact__name">Dov Strommen</p>
      <p class="contact__title">President &amp; CEO</p>
      <p class="contact__address">31 Harlow Ln,<br>Bexmoor, NJ 07813</p>
      <ul class="contact__list">
        <li class="contact__item">
          <svg class="contact__icon" viewBox="0 0 12 12" aria-hidden="true"><path d="M2.5 1 L4.5 1 L5.2 3.5 L4 4.5 C4.6 6 6 7.4 7.5 8 L8.5 6.8 L11 7.5 L11 9.5 C11 10.3 10.3 11 9.5 11 C5 11 1 7 1 2.5 C1 1.7 1.7 1 2.5 1 Z" fill="var(--leaf-green)"/></svg>
          <span>800-463-5918</span>
        </li>
        <li class="contact__item">
          <svg class="contact__icon" viewBox="0 0 12 12" aria-hidden="true"><rect x="0.5" y="2" width="11" height="8" rx="1" fill="var(--leaf-green)"/><path d="M1 2.5 L6 6.5 L11 2.5" stroke="var(--card-ground)" stroke-width="1" fill="none"/></svg>
          <span>dovstrommen@petalquarry.example</span>
        </li>
        <li class="contact__item">
          <svg class="contact__icon" viewBox="0 0 12 12" aria-hidden="true"><circle cx="6" cy="6" r="5.5" fill="var(--leaf-green)"/><path d="M0.5 6 H11.5 M6 0.5 C3.5 3 3.5 9 6 11.5 M6 0.5 C8.5 3 8.5 9 6 11.5" stroke="var(--card-ground)" stroke-width=".8" fill="none"/></svg>
          <span>www.petalquarry.example</span>
        </li>
      </ul>
    </div>
  </section>

  <section class="card card--back">
    <div class="back-brand">
      <span class="brand-name--back">Petal Quarry</span>
      <p class="tagline">The Professional Salon Source</p>
    </div>
  </section>
</main>
</body>
</html>
```